Custom Manufacturing Company square space website design

I own a custom manufacturing company that uses precision cutting technology to manufacture project components over a couple industries. We have an industrial CNC router and state of the art edge bander and cut a lot of cabinetry components for cabinet shops, builders, closet companies, ect. We offer design and assembly for any cabinetry or can build cabinets to spec. We also cut components for other industries out of wood, plastics, acryclics, ect. We offer design engineering services, product development protype services. we have a 3D printer farm. We want our communicate trust, dependability, and the value we place on client relationships.

We essentially want a credibility website. Landing page and drops downs for services we offer, capabilites, about us, contact

```html
<!DOCTYPE html>
<html lang="en">
<head>
<meta charset="utf-8">
<title>Riverbend CNC</title>
<link href="https://fonts.googleapis.com/css2?family=Michroma&family=Roboto:wght@400;500;700&display=swap" rel="stylesheet">
<style>
:root{
  --red:#e8202a;
  --blue:#0f72bb;
  --black:#000;
  --white:#fff;
  --ink:#222;
  --muted:#6b6b6b;
}
*{box-sizing:border-box;margin:0;padding:0}
html,body{width:1200px;height:4283px;overflow:hidden}
body{position:relative;font-family:'Roboto',sans-serif;color:var(--ink);background:var(--white)}
.abs{position:absolute}
.display{font-family:'Michroma',sans-serif;font-weight:400;letter-spacing:-1px;line-height:1;-webkit-text-stroke:1.2px currentColor}
.btn{position:absolute;background:var(--red);color:var(--white);font-weight:700;display:flex;align-items:center;justify-content:center;border-radius:2px}

/* header */
.site-header{position:absolute;left:0;top:0;width:1200px;height:85px;background:var(--white)}
.brand{position:absolute;left:108px;top:26px;display:flex;align-items:center;gap:10px;font-weight:700;font-size:18px;letter-spacing:1px;color:var(--ink)}
.brand-mark{width:30px;height:30px;border:3px solid var(--ink)}
.nav{position:absolute;top:36px;font-size:14px;color:var(--ink)}
.call-btn{left:854px;top:23px;width:235px;height:42px;font-size:13px;font-weight:500;gap:6px}

/* hero */
.hero{position:absolute;left:0;top:85px;width:1200px;height:678px;
  background:
    radial-gradient(ellipse 140px 170px at 1010px 480px,rgba(178,146,96,.95),rgba(178,146,96,0) 100%),
    radial-gradient(ellipse 300px 110px at 600px 510px,rgba(120,78,42,.95),rgba(120,78,42,.6) 60%,rgba(120,78,42,0) 100%),
    radial-gradient(ellipse 40px 60px at 480px 360px,rgba(245,240,228,.9),rgba(245,240,228,0)),
    linear-gradient(180deg,#e8e2d9 0%,#e6dfd5 62%,#d7cdbf 82%,#cfc4b4 100%)}
.hero-badge{left:111px;top:134px;width:193px;height:37px;background:var(--blue);color:var(--white);font-size:14px;font-weight:700;letter-spacing:4px;display:flex;align-items:center;justify-content:center}
.hero-title{left:111px;top:186px;font-size:44px;color:#1d1d1d;white-space:nowrap}
.hero-sub{left:111px;top:246px;font-size:21px;line-height:26px;color:#3a3a3a;width:420px}
.hero-btn{left:111px;top:319px;width:132px;height:38px;font-size:13px}
.slide-arrow{position:absolute;left:1124px;width:38px;height:38px;border-radius:50%;background:var(--white);display:flex;align-items:center;justify-content:center}

/* about */
.about-frame-red{left:103px;top:854px;width:160px;height:176px;border-left:3px solid var(--red);border-top:3px solid var(--red)}
.about-photo{left:120px;top:873px;width:420px;height:420px;background:linear-gradient(135deg,#9aa0a0,#c9bba6 55%,#8c8a84);border:2px solid #eee}
.about-frame-black{left:399px;top:1130px;width:158px;height:180px;border-right:7px solid var(--black);border-bottom:7px solid var(--black)}
.about-title{left:612px;top:872px;font-size:44px;color:var(--black)}
.about-text{left:612px;width:473px;font-size:13.5px;line-height:25.8px;color:var(--muted);text-align:justify}
.about-btn{left:612px;top:1280px;width:129px;height:38px;font-size:13px}

/* services */
.services{position:absolute;left:0;top:1413px;width:1200px;height:884px;background:var(--black)}
.services-title{left:0;width:1200px;top:1512px;text-align:center;font-size:44px;color:var(--white)}
.service-photo{position:absolute;top:1599px;height:304px}
.service-label{position:absolute;top:1903px;height:75px;width:362px;background:var(--red);color:var(--white);font-weight:700;font-size:19px;text-align:center;display:flex;align-items:center;justify-content:center;line-height:21px}
.video{left:111px;top:2056px;width:978px;height:482px;background:linear-gradient(90deg,#b7c3cf 0%,#e4e8ea 45%,#eeeeee 100%)}
.play{left:560px;top:2257px;width:80px;height:80px;border-radius:50%;background:rgba(232,32,42,.3);display:flex;align-items:center;justify-content:center}
.play span{width:60px;height:60px;border-radius:50%;background:var(--red);display:flex;align-items:center;justify-content:center}

/* components */
.tab{position:absolute;top:2658px;height:129px;width:600px;color:var(--white);font-weight:700;font-size:28px;display:flex;align-items:center;justify-content:center}
.tab-active{left:0;background:var(--black)}
.tab-alt{left:600px;background:var(--blue)}
.tab-pointer{left:286px;top:2786px}
.client-card{position:absolute;top:2850px;width:302px;height:348px;color:var(--white);font-weight:700;font-size:19px;display:flex;align-items:flex-end;justify-content:center;padding-bottom:40px}
.bar-bottom{border-bottom:8px solid var(--red);height:356px}
.bar-top{position:absolute;left:449px;top:2842px;width:302px;height:8px;background:var(--red)}

/* contact */
.contact-base{position:absolute;left:0;top:3711px;width:1200px;height:572px;background:var(--black)}
.contact-box{left:111px;top:3317px;width:978px;height:551px;background:var(--blue)}
.contact-title{left:111px;width:978px;top:3387px;text-align:center;font-size:42px;color:var(--white)}
.field{position:absolute;border:2px solid var(--white);color:var(--white);font-size:13px;padding-left:22px}
.field-line{top:3474px;height:62px;width:280px;display:flex;align-items:center}
.field-area{left:161px;top:3557px;width:878px;height:129px;padding-top:22px}
.submit{left:460px;top:3711px;width:280px;height:63px;font-size:13px}

/* footer */
.foot-head{position:absolute;top:3970px;color:var(--white);font-weight:700;font-size:21px}
.foot-list{position:absolute;top:4008px;list-style:none;color:var(--white);font-size:14px;line-height:25.8px}
.foot-list li{display:flex;align-items:center;gap:12px}
.chev{font-size:12px;width:14px}
.social{position:absolute;top:4009px;width:33px;height:33px;background:var(--white);display:flex;align-items:center;justify-content:center}
.social i{width:11px;height:11px;border:2px solid #111;border-radius:50%;display:block}
.copyright{left:0;width:1200px;top:4184px;text-align:center;color:var(--white);font-size:13px}
</style>
</head>
<body>

<header class="site-header">
  <div class="brand"><span class="brand-mark"></span>RIVERBEND CNC</div>
  <nav>
    <span class="nav" style="left:354px">Home</span>
    <span class="nav" style="left:430px">Services we offer</span>
    <span class="nav" style="left:573px">Capabilities</span>
    <span class="nav" style="left:686px">About us</span>
    <span class="nav" style="left:779px">Contact</span>
  </nav>
  <div class="btn call-btn">
    <svg width="13" height="13" viewBox="0 0 24 24"><path fill="#fff" d="M6.6 10.8a15 15 0 0 0 6.6 6.6l2.2-2.2c.3-.3.7-.4 1-.2 1.1.4 2.3.6 3.6.6.6 0 1 .4 1 1V20c0 .6-.4 1-1 1A17 17 0 0 1 3 4c0-.6.4-1 1-1h3.5c.6 0 1 .4 1 1 0 1.3.2 2.5.6 3.6.1.3 0 .7-.2 1z"/></svg>
    Call Us : <b>+1 888 888 8888</b>
  </div>
</header>

<section class="hero" role="img" aria-label="Living room with wooden sideboard, table lamp and tan lounge chair">
  <div class="abs hero-badge">WELCOME TO</div>
  <h1 class="abs display hero-title">RIVERBEND CNC</h1>
  <p class="abs hero-sub">Lorem ipsum dolor sit amet, consectetur adipiscing elit, sed do eiusmod</p>
  <div class="btn hero-btn">GET STARTED</div>
  <div class="slide-arrow" style="top:306px"><svg width="14" height="14" viewBox="0 0 14 14"><path d="M3 9l4-4 4 4" fill="none" stroke="#111" stroke-width="1.6"/></svg></div>
  <div class="slide-arrow" style="top:357px"><svg width="14" height="14" viewBox="0 0 14 14"><path d="M3 5l4 4 4-4" fill="none" stroke="#111" stroke-width="1.6"/></svg></div>
</section>

<section class="about">
  <div class="abs about-frame-red"></div>
  <div class="abs about-photo" role="img" aria-label="Interior with shelving, cabinet and armchair"></div>
  <div class="abs about-frame-black"></div>
  <h2 class="abs display about-title">ABOUT US</h2>
  <p class="abs about-text" style="top:944px">Lorem ipsum dolor sit amet, consectetur adipiscing elit, sed do eiusmod tempor incididunt ut labore et dolore magna aliqua. Ut enim ad minim veniam, quis nostrud exercitation ullamco laboris nisi ut aliquip ex ea commodo consequat. Duis aute irure dolor in reprehenderit in voluptate velit esse cillum dolore eu fugiat nulla pariatur.</p>
  <p class="abs about-text" style="top:1098px">Excepteur sint occaecat cupidatat non proident, sunt in culpa qui officia deserunt mollit anim id est laborum. Lorem ipsum dolor sit amet, consectetur adipiscing elit, sed do eiusmod tempor incididunt ut labore et dolore magna aliqua. Ut enim ad minim veniam, quis nostrud exercitation ullamco laboris nisi ut aliquip ex ea commodo consequat. Duis aute irure dolor in reprehenderit in voluptate velit esse cillum dolore</p>
  <div class="btn about-btn">READ MORE</div>
</section>

<section class="services"></section>
<h2 class="abs display services-title">OUR SERVICES</h2>
<div class="service-photo" style="left:103px;width:487px;background:linear-gradient(135deg,#8d8f8c,#e2e0da 50%,#9a9c96)" role="img" aria-label="Two engineers reviewing a tablet in an office"></div>
<div class="service-photo" style="left:608px;width:489px;background:linear-gradient(135deg,#4f5d78,#dfe3e6 45%,#c9a36e 80%,#b92a2a)" role="img" aria-label="Team sketching product prototypes on paper"></div>
<div class="service-label" style="left:166px">DESIGN ENGINEERING SERVICES</div>
<div class="service-label" style="left:671px">PRODUCT DEVELOPMENT<br>PROTOTYPE SERVICES</div>
<div class="abs video" role="img" aria-label="Modern white kitchen with city view, video preview"></div>
<div class="abs play"><span><svg width="18" height="20" viewBox="0 0 18 20"><path d="M2 1l15 9-15 9z" fill="#fff"/></svg></span></div>

<div class="tab tab-active">CABINETRY COMPONENTS</div>
<div class="tab tab-alt">CUT COMPONENTS</div>
<svg class="abs tab-pointer" width="30" height="31" viewBox="0 0 30 31"><path d="M0 0h30L15 31z" fill="#000"/></svg>

<div class="bar-top"></div>
<div class="client-card bar-bottom" style="left:111px;background:linear-gradient(180deg,#d8d4cc,#8a7f70)" role="img" aria-label="Pantry with shelving and ladder">CABINET SHOPS</div>
<div class="client-card" style="left:449px;background:linear-gradient(180deg,#6f7479,#3c3d30 70%,#2a2a22)" role="img" aria-label="Builder in hard hat at a construction site">BUILDERS</div>
<div class="client-card bar-bottom" style="left:786px;background:linear-gradient(180deg,#9b8873,#4a3d34)" role="img" aria-label="Closet showroom with display shelving">CLOSET COMPANIES</div>

<div class="contact-base"></div>
<section class="abs contact-box"></section>
<h2 class="abs display contact-title">CONTACT US</h2>
<div class="field field-line" style="left:161px">Name</div>
<div class="field field-line" style="left:460px">Email</div>
<div class="field field-line" style="left:760px">Phone</div>
<div class="field field-area">Message</div>
<div class="btn submit">SUBMIT NOW</div>

<footer>
  <h3 class="foot-head" style="left:111px">LINKS</h3>
  <ul class="foot-list" style="left:111px">
    <li><span class="chev">»</span>Home</li>
    <li><span class="chev">»</span>About</li>
    <li><span class="chev">»</span>Services we offer</li>
    <li><span class="chev">»</span>Contact</li>
  </ul>
  <h3 class="foot-head" style="left:354px">INFORMATION</h3>
  <ul class="foot-list" style="left:354px">
    <li><span class="chev">»</span>About</li>
    <li><span class="chev">»</span>Capabilities</li>
    <li><span class="chev">»</span>Privacy Policy</li>
    <li><span class="chev">»</span>Terms of Condition</li>
  </ul>
  <h3 class="foot-head" style="left:650px">SUPPORT</h3>
  <ul class="foot-list" style="left:650px">
    <li><svg class="chev" width="12" height="14" viewBox="0 0 12 14"><path d="M6 0a5 5 0 0 0-5 5c0 4 5 9 5 9s5-5 5-9a5 5 0 0 0-5-5zm0 7a2 2 0 1 1 0-4 2 2 0 0 1 0 4z" fill="#e8202a"/></svg>Lorem ipsum dolor sit amet</li>
    <li><svg class="chev" width="13" height="13" viewBox="0 0 24 24"><path fill="#e8202a" d="M6.6 10.8a15 15 0 0 0 6.6 6.6l2.2-2.2c.3-.3.7-.4 1-.2 1.1.4 2.3.6 3.6.6.6 0 1 .4 1 1V20c0 .6-.4 1-1 1A17 17 0 0 1 3 4c0-.6.4-1 1-1h3.5c.6 0 1 .4 1 1 0 1.3.2 2.5.6 3.6.1.3 0 .7-.2 1z"/></svg>+1 888 888 8888</li>
    <li><svg class="chev" width="14" height="11" viewBox="0 0 14 11"><rect width="14" height="11" fill="#e8202a"/><path d="M0 0l7 6 7-6" fill="none" stroke="#000" stroke-width="1.2"/></svg>info@companyname.com</li>
  </ul>
  <h3 class="foot-head" style="left:947px">FOLLOW US</h3>
  <div class="social" style="left:949px" aria-label="Social link"><i></i></div>
  <div class="social" style="left:989px" aria-label="Social link"><i></i></div>
  <div class="social" style="left:1029px" aria-label="Social link"><i></i></div>
  <div class="social" style="left:1069px" aria-label="Social link"><i></i></div>
  <p class="abs copyright">© Copyrights Company name 2023. All rights reserved</p>
</footer>

</body>
</html>
```